Business Card for Coastal Tundrabridge Advisory

We need a business card for Coastal Tundrabridge Advisory. The company website address is provided below. The company logo is attached. We provide specialized permafrost services to the mining, transportation, and oil & gas industries. The card should be prepared for:
Matthias Korhonen, PhD.
Coastal Tundrabridge Advisory
PO Box 418259
Quillwater, Alaska 99642
Direct: +1-907-555-0143
Email: mkorhonen@tundrabridgeadvisory.example
Website: www.coastaltundrabridgeadvisory.example

```html
<!DOCTYPE html>
<html lang="en">
<head>
<meta charset="utf-8">
<title>Coastal Tundrabridge Advisory — Business Card</title>
<link rel="stylesheet" href="https://fonts.googleapis.com/css2?family=Lato:wght@400;700;900&display=swap">
<style>
  :root {
    --stage: #2c2e31;
    --card-light: #ffffff;
    --card-dark: #111821;
    --ink: #131a22;
    --ink-soft: #6b6f74;
    --rule-grey: #8a8d90;
  }
  * { box-sizing: border-box; margin: 0; padding: 0; }
  html, body { width: 1200px; height: 952px; overflow: hidden; }
  body {
    background: var(--stage);
    font-family: "Lato", sans-serif;
    position: relative;
  }
  .card {
    position: absolute;
    top: 327px;
    width: 520px;
    height: 298px;
    border-radius: 3px;
    box-shadow: 0 18px 40px rgba(0,0,0,.45);
    overflow: hidden;
  }
  .card--front { left: 40px; background: var(--card-light); color: var(--ink); }
  .card--back { left: 640px; background: var(--card-dark); }

  .side-rule { position: absolute; left: 0; top: 0; }

  .wordmark {
    font-weight: 900;
    text-transform: uppercase;
    letter-spacing: 1px;
    white-space: nowrap;
  }
  .card--front .wordmark {
    position: absolute;
    top: 30px; left: 72px;
    font-size: 21px;
    color: var(--ink);
  }
  .card--back .wordmark {
    position: absolute;
    top: 50%; left: 50%;
    transform: translate(-50%, -50%);
    font-size: 21px;
    color: #ffffff;
  }

  .contact {
    position: absolute;
    left: 72px; top: 92px;
    font-size: 11px;
    color: var(--ink-soft);
    line-height: 1.6;
  }
  .contact__name {
    font-size: 16px;
    font-weight: 700;
    color: var(--ink);
    letter-spacing: .3px;
    text-transform: uppercase;
  }
  .contact__name strong { font-weight: 900; }
  .contact__company { margin-bottom: 6px; }
  .contact__row { display: flex; align-items: center; gap: 14px; }
  .contact__item { display: flex; align-items: center; gap: 5px; }
  .contact__icon {
    width: 13px; height: 13px;
    background: var(--ink);
    border-radius: 2px;
    display: inline-flex; align-items: center; justify-content: center;
  }
  .contact__address { margin-top: 2px; }
  .contact__web {
    margin-top: 10px;
    font-size: 12px;
    letter-spacing: 2.2px;
    color: var(--ink);
    font-weight: 700;
  }
  .contact__web span { color: var(--ink-soft); font-weight: 400; }
</style>
</head>
<body>

<section class="card card--front" aria-label="Business card front">
  <svg class="side-rule" width="60" height="298" viewBox="0 0 60 298" aria-hidden="true">
    <rect x="40" y="40" width="3" height="150" fill="var(--rule-grey)"/>
    <polygon points="40,196 43,196 49,206 49,298 40,298" fill="var(--ink)"/>
  </svg>

  <div class="wordmark">Coastal Tundrabridge Advisory</div>

  <div class="contact">
    <div class="contact__name">Matthias <strong>Korhonen, PhD</strong></div>
    <div class="contact__company">Coastal Tundrabridge Advisory</div>
    <div class="contact__row">
      <span class="contact__item">
        <span class="contact__icon">
          <svg width="9" height="9" viewBox="0 0 24 24" aria-hidden="true"><path fill="#fff" d="M6.6 10.8a15 15 0 0 0 6.6 6.6l2.2-2.2c.3-.3.7-.4 1-.2 1.1.4 2.3.6 3.6.6.6 0 1 .4 1 1V20c0 .6-.4 1-1 1A17 17 0 0 1 3 4c0-.6.4-1 1-1h3.5c.6 0 1 .4 1 1 0 1.3.2 2.5.6 3.6.1.3 0 .7-.2 1z"/></svg>
        </span>
        +1-907-555-0143
      </span>
      <span class="contact__item">
        <span class="contact__icon">
          <svg width="9" height="9" viewBox="0 0 24 24" aria-hidden="true"><path fill="#fff" d="M2 5h20v14H2z"/><path fill="none" stroke="#131a22" stroke-width="2" d="M2 5l10 8 10-8"/></svg>
        </span>
        mkorhonen@tundrabridgeadvisory.example
      </span>
    </div>
    <div class="contact__address">PO Box 418259, Quillwater, Alaska 99642</div>
    <div class="contact__web">www.<strong>coastaltundrabridgeadvisory</strong><span>.example</span></div>
  </div>
</section>

<section class="card card--back" aria-label="Business card back">
  <div class="wordmark">Coastal Tundrabridge Advisory</div>
</section>

</body>
</html>
```